TEBSIRK HOA Portal Site for Public

Clean up and organize current website; need website to look good and functional; this is a HOA (homeowner association management) website where homeowners can login and pay their bill, general information about a HOA, monthly newsletter page.
Competitors:
https://quillmarsh.example/
https://dorvinpalms.example/
https://www.kelbrookhomes.example/nevada
http://www.tpw-hoa.example/

Target Market(s)

homeowners

Industry/Entity Type

Real Estate

Coding

Coded - Design and coding required

Number of Pages Required

5+ page

Font styles to use
Serif

Colors
0292cd
33a6d7
e667a6
e34297

Requirements
Must have
• login to pay
• services page
• contact us
• order resale package
Nice to have
• page why an HOA would contract us

```html
<!DOCTYPE html>
<html lang="en">
<head>
<meta charset="utf-8">
<title>TEBSIRK HOA</title>
<link href="https://fonts.googleapis.com/css2?family=Montserrat:wght@600;700&family=Nunito+Sans:wght@300;400;600&family=Oswald:wght@400&display=swap" rel="stylesheet">
<style>
:root{
  --blue:#0292cd;
  --blue-light:#33a6d7;
  --blue-deep:#0a78ad;
  --pink:#e34297;
  --pink-light:#e667a6;
  --pink-pale:#ef97c4;
  --ink:#222;
  --muted:#8a8a8a;
  --pale:#f8f8f8;
}
*{box-sizing:border-box;margin:0;padding:0}
html,body{width:1200px;height:2745px;overflow:hidden;background:#fff}
body{position:relative;font-family:"Nunito Sans",sans-serif;color:var(--muted)}
.abs{position:absolute}
.btn{position:absolute;display:flex;align-items:center;justify-content:center;color:#fff;font-family:"Nunito Sans",sans-serif;font-weight:600;font-size:15px;letter-spacing:.5px;background:linear-gradient(90deg,var(--pink),var(--pink-pale));width:146px;height:52px}
.wordmark{font-family:"Oswald",sans-serif;font-size:34px;color:var(--ink);letter-spacing:.5px}
.heading{font-family:"Montserrat",sans-serif;font-weight:700;color:var(--ink)}

/* header */
.site-header{left:0;top:0;width:1200px;height:104px;background:#fff}
.site-header .wordmark{left:79px;top:27px}
.main-nav{left:338px;top:0;width:862px;height:104px;background:linear-gradient(90deg,var(--blue-light),var(--blue-deep));display:flex;align-items:center;padding-left:18px;gap:36px;color:#fff;font-size:17px}
.main-nav span{position:relative}
.main-nav .active{font-weight:700}
.main-nav .active::after{content:"";position:absolute;left:0;right:0;bottom:-39px;height:3px;background:#fff}

/* hero */
.hero{left:0;top:104px;width:1200px;height:573px;background:linear-gradient(135deg,#4d5a3a 0%,#6e7550 30%,#5a5a52 50%,#7b8a4c 75%,#5d6240 100%)}
.pale-band{left:0;top:677px;width:1200px;height:562px;background:var(--pale)}

/* offer card */
.offer-card{left:77px;top:615px;width:1046px;height:552px;background:#fff;box-shadow:0 4px 18px rgba(0,0,0,.05);text-align:center}
.offer-card .bar{height:10px;background:linear-gradient(90deg,var(--pink),var(--pink-pale))}
.offer-card h2{font-size:42px;margin-top:46px}
.offer-list{margin-top:30px;font-size:14.5px;line-height:23px;color:var(--muted)}
.offer-list p{margin:0 auto 13.5px;width:680px}
.offer-card .btn{left:450px;top:447px}

/* feature panels */
.feature-bg{top:1239px;width:600px;height:469px}
.feature-bg.left{left:0;background:linear-gradient(135deg,#8a6a4c,#9aa0a8 50%,#6e7a5a)}
.feature-bg.right{left:600px;background:linear-gradient(135deg,#6b7a8c,#8e9aa6 45%,#6a8a4c)}
.feature-box{top:1302px;width:445px;height:344px;background:linear-gradient(135deg,rgba(2,146,205,.92),rgba(51,166,215,.88));color:#fff;text-align:center}
.feature-box svg{position:absolute;left:50%;margin-left:-45px;top:30px}
.feature-box h3{font-family:"Montserrat",sans-serif;font-weight:600;font-size:19px;line-height:26px;position:absolute;left:20px;right:20px;top:124px}
.feature-box p{position:absolute;left:28px;right:28px;font-size:14.5px;line-height:26px}
.feature-box .btn{left:150px;top:260px}

/* resale */
.resale h2{left:79px;top:1748px;font-size:44px;line-height:47px}
.resale p{left:79px;top:1878px;width:495px;font-size:15px;line-height:26px}
.resale .btn{left:77px;top:2063px}
.resale-photo{left:623px;top:1750px;width:500px;height:364px;background:linear-gradient(135deg,#c9ccd0,#d6b77a 55%,#b89a4a 80%,#8e9096)}

/* newsletter */
.newsletter{left:0;top:2177px;width:1200px;height:197px;background:linear-gradient(90deg,var(--blue-light),var(--blue-deep))}
.newsletter .stripe{position:absolute;left:0;width:1200px;height:10px;background:linear-gradient(90deg,var(--pink),var(--pink-pale))}
.newsletter h3{position:absolute;left:79px;top:60px;font-weight:400;font-size:29px;color:#fff}
.newsletter small{position:absolute;left:79px;top:108px;font-size:14.5px;color:#fff}
.email-field{position:absolute;left:556px;top:63px;width:396px;height:62px;border:1px solid #fff;color:#fff;font-size:16px;padding:20px 14px}
.subscribe{position:absolute;left:962px;top:63px;width:161px;height:62px;background:#fff;color:#111;font-size:14px;font-weight:600;display:flex;align-items:center;justify-content:center}

/* footer */
.footer-col{top:2415px}
.footer-col h4{font-family:"Montserrat",sans-serif;font-weight:700;font-size:23px;color:var(--ink);margin-bottom:22px}
.footer-col .wordmark{display:block;margin-top:-8px;margin-bottom:14px}
.footer-col p{font-size:14.5px;line-height:26px}
.map-link{display:flex;align-items:center;gap:14px;margin-top:14px;width:240px;height:46px;border:1px solid #e5e5e5;border-radius:23px;padding-left:12px;font-size:13.5px;font-weight:600;color:var(--blue)}
.quick li{list-style:none;font-size:14.5px;line-height:31.5px}
.quick li::before{content:"- ";}
.quick li.active{color:var(--pink);font-weight:600}
.contact-row{display:flex;gap:14px;font-size:14.5px;line-height:26px;margin-bottom:14px}
.social-row{display:flex;align-items:center;gap:18px;margin-bottom:6px;font-size:14.5px}
.social-row i{display:block;width:36px;height:36px}
.rule{left:77px;top:2664px;width:1046px;height:1px;background:#e8e8e8}
.copyright{left:0;top:2696px;width:1200px;text-align:center;font-size:13.5px}
.copyright b{color:var(--muted);font-weight:600}
</style>
</head>
<body>

<header class="site-header abs">
  <div class="wordmark abs">TEBSIRK HOA</div>
</header>
<nav class="main-nav abs">
  <span class="active">Home</span>
  <span>Services</span>
  <span>Why an HOA would contract us</span>
  <span>Order resale package</span>
  <span>Contact Us</span>
</nav>

<div class="hero abs" role="img" aria-label="Aerial view of a residential neighbourhood with houses, trees and streets"></div>
<div class="pale-band abs"></div>

<section class="offer-card abs">
  <div class="bar"></div>
  <h2 class="heading">What We Offer</h2>
  <div class="offer-list">
    <p>Accessible, licensed Association Managers</p>
    <p>24 hour Web site access: online account information</p>
    <p>24 hour emergency service</p>
    <p>Provide monthly financial reports to the Board of Directors</p>
    <p style="width:660px">Read, study and understand all governing documents of the Association. Correspond with members in violation of the CC&amp;Rs, By-laws, Rules &amp; Regulations and report the status of all noncompliance to the Board of Directors in a timely manner.</p>
    <p style="width:570px">Act as the custodian of the corporate records. Coordinate preparing annual tax returns for the Association.</p>
  </div>
  <div class="btn">READ MORE</div>
</section>

<div class="feature-bg left abs" role="img" aria-label="Suburban street lined with houses and trees"></div>
<div class="feature-bg right abs" role="img" aria-label="Modern home with lawn and hills behind"></div>

<section class="feature-box abs" style="left:77px">
  <svg width="90" height="72" viewBox="0 0 90 72" fill="none" stroke="#fff" stroke-width="2">
    <path d="M8 28 L20 4 H70 L82 28 Z"/>
    <path d="M14 28 V62 H76 V28"/>
    <rect x="22" y="36" width="20" height="12"/>
    <rect x="52" y="38" width="14" height="24"/>
    <circle cx="10" cy="52" r="6"/><path d="M10 58 V70"/>
    <circle cx="82" cy="46" r="6"/><path d="M82 52 V64"/>
  </svg>
  <h3>Association Management Services</h3>
  <p style="top:164px">Lorem ipsum dolor sit amet, consectetur adipiscing elit, sed do thereof eiusmod tempor incididunt ut labore et dolore magna aliqua. Ut enim ad minim veniam.</p>
  <div class="btn">READ MORE</div>
</section>

<section class="feature-box abs" style="left:677px">
  <svg width="90" height="72" viewBox="0 0 90 72" fill="none" stroke="#fff" stroke-width="2">
    <circle cx="32" cy="18" r="13"/>
    <path d="M8 68 V58 Q8 40 32 40 Q44 40 50 46"/>
    <circle cx="60" cy="56" r="9"/>
    <circle cx="60" cy="56" r="3.5"/>
    <path d="M60 43 V47 M60 65 V69 M47 56 H51 M69 56 H73 M51 47 L54 50 M66 62 L69 65 M51 65 L54 62 M66 50 L69 47"/>
  </svg>
  <h3>TEBCO manages communities throughout Southern Nevada</h3>
  <p style="top:190px">Lorem ipsum dolor sit amet, consectetur adipiscing elit, sed do thereof eiusmod tempor incididunt.</p>
  <div class="btn">READ MORE</div>
</section>

<section class="resale">
  <h2 class="heading abs">Order Resale<br>Package</h2>
  <p class="abs">Lorem ipsum dolor sit amet, consectetur adipiscing elit, sed doe there eiusmod tempor incididunt ut labore et dolore magna aliqua. Ut enim ad minim veniam, quis nostrud exercitation ullamco laboris nisi ut the aliquip ex ea commodo consequat. Duis aute irure dolor in of the part reprehenderit in voluptate velit esse cillum dolore eu fugiat nulla waer pariatur. Excepteur sint occaecat cupidatat non proident.</p>
  <div class="btn">READ MORE</div>
  <div class="resale-photo abs" role="img" aria-label="Couple holding a small model house and keys after buying a home"></div>
</section>

<section class="newsletter abs">
  <div class="stripe" style="top:0"></div>
  <h3>Get news directly to your email</h3>
  <small>we will only send your important updates and notices.</small>
  <div class="email-field">Your Email Address :</div>
  <div class="subscribe">SUBSCRIBE</div>
  <div class="stripe" style="bottom:0"></div>
</section>

<footer>
  <div class="footer-col abs" style="left:79px;width:240px">
    <span class="wordmark">TEBSIRK HOA</span>
    <p>Lorem ipsum damet, consectetur adipiscing elit, eiusmod tempor incididunt ut labore .</p>
    <div class="map-link">Get directions on the map
      <svg width="26" height="10" viewBox="0 0 26 10" fill="none" stroke="var(--pink)" stroke-width="1.6"><path d="M0 5 H24 M19 1 L24 5 L19 9"/></svg>
    </div>
  </div>
  <div class="footer-col abs" style="left:348px">
    <h4>Quick Links</h4>
    <ul class="quick">
      <li class="active">Home</li>
      <li>Services</li>
      <li>Why an HOA would contract us</li>
      <li>Order resale package</li>
      <li>Contact Us</li>
    </ul>
  </div>
  <div class="footer-col abs" style="left:616px">
    <h4>Get In Touch</h4>
    <div class="contact-row">
      <svg width="22" height="22" viewBox="0 0 24 24" fill="var(--pink)"><path d="M6.6 10.8a15 15 0 0 0 6.6 6.6l2.2-2.2a1 1 0 0 1 1-.25 11.4 11.4 0 0 0 3.6.57 1 1 0 0 1 1 1V20a1 1 0 0 1-1 1A17 17 0 0 1 3 4a1 1 0 0 1 1-1h3.5a1 1 0 0 1 1 1c0 1.25.2 2.45.57 3.57a1 1 0 0 1-.25 1z"/></svg>
      <span>123.456.7890</span>
    </div>
    <div class="contact-row">
      <svg width="22" height="22" viewBox="0 0 24 24" fill="var(--pink)"><path d="M2 5h20v14H2z"/><path d="M2 5l10 8 10-8" stroke="#fff" stroke-width="1.6" fill="none"/></svg>
      <span>info@tebsirkhoa.example</span>
    </div>
    <div class="contact-row">
      <svg width="22" height="22" viewBox="0 0 24 24" fill="var(--pink)"><path d="M12 2a7 7 0 0 0-7 7c0 5 7 13 7 13s7-8 7-13a7 7 0 0 0-7-7zm0 9.5A2.5 2.5 0 1 1 12 6.5a2.5 2.5 0 0 1 0 5z"/></svg>
      <span>123, Address, State Name,<br>City Name,Zipcode</span>
    </div>
  </div>
  <div class="footer-col abs" style="left:884px">
    <h4>follow Us</h4>
    <div class="social-row"><i style="background:#3b5a9a"></i>Neighborly</div>
    <div class="social-row"><i style="background:#1da1e0"></i>Chirpline</div>
    <div class="social-row"><i style="background:#1478b8"></i>Searchpath</div>
  </div>
  <div class="rule abs"></div>
  <div class="copyright abs">Copyright © <b>TEBSIRK HOA</b> - 2019 . All Right Reserved</div>
</footer>

</body>
</html>
```